Velborix advertisement one page flyer design

We need a flyer design for our company to advertise what we offer, it only needs to be one sided, approx A5 in size.
Our logo: http://velborix-example.com/images/logo.png (I will provide in high-res later)
We offer, website design, development, bespoke applications. We would like to advertise that we can be hired for short term contracts for companies who need help with their work load.
Some of, but not limited to the systems we build are content management systems, e-commerce systems & event booking systems.
Our strap line is "We design, develop and deliver", a nice sleek redesign of the image on our website would be nice, but not required 100% - http://velborix-example.com/
Other details to put on the flyer:-
Email: hello@velborix-example.com
Tel: 01632 960 417
Address: Velborix Ltd, Crest Suites, Dunmoor Road, Cheltenham, GL53 4QT
We welcome any other ideas.

```html
<!DOCTYPE html>
<html lang="en">
<head>
<meta charset="utf-8">
<title>Velborix – Web Design, Development &amp; Delivery</title>
<link rel="stylesheet" href="https://fonts.googleapis.com/css2?family=Kalam:wght@700&family=Sarpanch:wght@700;800&family=Roboto+Condensed:wght@700&family=Arimo:wght@400&display=swap">
<style>
  :root {
    --page-bg: #e9e6e2;
    --orange: #e67817;
    --orange-deep: #b24408;
    --orange-dark: #6e1d04;
    --orange-light: #f6b35a;
    --panel-grey: #9b9b9b;
    --ink: #262626;
    --white: #ffffff;
  }
  * { box-sizing: border-box; margin: 0; padding: 0; }
  html, body { width: 891px; height: 1200px; overflow: hidden; background: var(--page-bg); }

  .flyer {
    position: absolute; left: 57px; top: 47px;
    width: 778px; height: 1105px;
    background: var(--panel-grey);
    box-shadow: 0 2px 10px rgba(0,0,0,.18);
  }

  /* Hero */
  .hero { position: absolute; left: 0; top: 0; width: 778px; height: 481px; overflow: hidden; }
  .hero-visual {
    position: absolute; inset: 0;
    background:
      radial-gradient(ellipse 300px 260px at 640px 190px, var(--orange-light) 0%, rgba(246,179,90,0) 70%),
      radial-gradient(ellipse 420px 380px at 600px 300px, #e98a2a 0%, rgba(233,138,42,0) 75%),
      linear-gradient(100deg, var(--orange-dark) 0%, var(--orange-deep) 35%, var(--orange) 70%, #d9641a 100%);
  }
  .brand {
    position: absolute; left: 48px; top: 48px;
    font-family: "Kalam", cursive; font-weight: 700;
    font-size: 68px; line-height: 1; color: var(--white);
  }
  .hero-copy {
    position: absolute; left: 46px; top: 184px; width: 540px;
    font-family: "Kalam", cursive; font-weight: 700;
    font-size: 24px; line-height: 40px; color: var(--white);
  }
  .hero-copy p + p { margin-top: 28px; }

  /* How it works */
  .section-title {
    position: absolute;
    font-family: "Kalam", cursive; font-weight: 700;
    color: var(--ink); letter-spacing: 1px;
  }
  .process-title { left: 46px; top: 530px; font-size: 31px; }
  .solutions-title { left: 448px; top: 534px; font-size: 26px; }

  .divider { position: absolute; left: 387px; top: 538px; width: 3px; height: 448px; background: var(--orange); }

  .drop {
    position: absolute; background: var(--orange);
    border-radius: 50% 0 50% 50%;
    display: flex; align-items: center; justify-content: center;
  }
  .drop svg { display: block; }

  .step { position: absolute; left: 38px; width: 300px; height: 110px; }
  .step .drop { left: 8px; top: 0; width: 106px; height: 106px; }
  .step-label {
    position: absolute; left: 122px; top: 6px;
    font-family: "Sarpanch", sans-serif; font-weight: 800; color: var(--ink);
    line-height: .9;
  }
  .step-label small { display: block; font-size: 26px; }
  .step-label strong { display: block; font-size: 52px; letter-spacing: -1px; }
  .step-design { top: 590px; }
  .step-develop { top: 738px; }
  .step-deliver { top: 885px; }

  /* Solutions */
  .solutions { position: absolute; left: 448px; top: 590px; list-style: none; }
  .solution { position: relative; height: 67.5px; }
  .solution .drop { left: 0; top: 0; width: 62px; height: 62px; }
  .solution-name {
    position: absolute; left: 73px; top: 15px; white-space: nowrap;
    font-family: "Roboto Condensed", sans-serif; font-weight: 700;
    font-size: 22px; color: var(--ink);
  }

  /* Contact */
  .contact {
    position: absolute; left: 0; bottom: 0; width: 778px; height: 80px;
    background: var(--orange); color: var(--white);
    font-family: "Arimo", Arial, sans-serif; text-align: center;
  }
  .contact-line { display: flex; justify-content: center; align-items: center; gap: 8px; }
  .contact-primary { font-size: 25px; padding-top: 12px; gap: 10px; }
  .contact-primary .gap { width: 16px; }
  .contact-address { font-size: 19px; padding-top: 6px; }
</style>
</head>
<body>
<main class="flyer">
  <section class="hero">
    <div class="hero-visual" role="img" aria-label="Warm orange photo of a hand touching glowing web interface tiles marked http, www and php"></div>
    <h1 class="brand">Velborix</h1>
    <div class="hero-copy">
      <p>We offer website design,<br>development, bespoke application</p>
      <p>We can be hired for short term contract<br>for. companies who need help with<br>then work load</p>
    </div>
  </section>

  <h2 class="section-title process-title">How It Works?</h2>
  <div class="divider"></div>

  <div class="step step-design">
    <div class="drop">
      <svg width="62" height="62" viewBox="0 0 62 62" fill="none" stroke="#fff" stroke-width="7" stroke-linecap="round">
        <line x1="12" y1="50" x2="48" y2="14"/><line x1="14" y1="12" x2="50" y2="48"/>
      </svg>
    </div>
    <div class="step-label"><small>we</small><strong>design</strong></div>
  </div>

  <div class="step step-develop">
    <div class="drop">
      <svg width="62" height="62" viewBox="0 0 62 62" fill="none" stroke="#fff" stroke-width="7" stroke-linecap="round">
        <line x1="14" y1="48" x2="46" y2="16"/><circle cx="48" cy="14" r="7" stroke-width="5"/>
        <line x1="14" y1="14" x2="48" y2="48"/>
      </svg>
    </div>
    <div class="step-label"><small>we</small><strong>devlop</strong></div>
  </div>

  <div class="step step-deliver">
    <div class="drop">
      <svg width="62" height="62" viewBox="0 0 62 62" fill="#fff">
        <rect x="24" y="18" width="22" height="14"/><rect x="24" y="34" width="26" height="12"/>
        <rect x="16" y="10" width="5" height="40"/><rect x="16" y="46" width="36" height="4"/>
        <circle cx="20" cy="54" r="5"/>
      </svg>
    </div>
    <div class="step-label"><small>we</small><strong>deliver</strong></div>
  </div>

  <h2 class="section-title solutions-title">Solutions We Provide</h2>
  <ul class="solutions">
    <li class="solution"><div class="drop"><svg width="30" height="30" viewBox="0 0 30 30" fill="none" stroke="#fff" stroke-width="3"><rect x="6" y="3" width="18" height="24"/><line x1="10" y1="11" x2="20" y2="11"/><line x1="10" y1="17" x2="20" y2="17"/></svg></div><span class="solution-name">Content Management</span></li>
    <li class="solution"><div class="drop"><svg width="32" height="32" viewBox="0 0 32 32" fill="none" stroke="#fff" stroke-width="2.5"><circle cx="16" cy="16" r="12"/><ellipse cx="16" cy="16" rx="5" ry="12"/><line x1="4" y1="16" x2="28" y2="16"/></svg></div><span class="solution-name">Web Design</span></li>
    <li class="solution"><div class="drop"><svg width="30" height="30" viewBox="0 0 30 30" fill="none" stroke="#fff" stroke-width="2.5"><circle cx="15" cy="15" r="11"/><path d="M15 9a6 6 0 1 1-6 6"/></svg></div><span class="solution-name">Bespoke System</span></li>
    <li class="solution"><div class="drop"><svg width="32" height="32" viewBox="0 0 32 32" fill="none" stroke="#fff" stroke-width="2.5"><circle cx="16" cy="16" r="12"/><ellipse cx="16" cy="16" rx="5" ry="12"/><line x1="4" y1="16" x2="28" y2="16"/></svg></div><span class="solution-name">e-commerce</span></li>
    <li class="solution"><div class="drop"><svg width="30" height="30" viewBox="0 0 30 30" fill="none" stroke="#fff" stroke-width="2.5"><rect x="5" y="9" width="16" height="16"/><path d="M10 17l3 3 11-14"/></svg></div><span class="solution-name">Subscription System</span></li>
    <li class="solution"><div class="drop"><svg width="30" height="30" viewBox="0 0 30 30" fill="#fff"><rect x="5" y="8" width="20" height="5"/><rect x="5" y="15" width="20" height="5"/><rect x="5" y="22" width="20" height="5"/></svg></div><span class="solution-name">Domain &amp; Hosting</span></li>
  </ul>

  <footer class="contact">
    <div class="contact-line contact-primary">
      <svg width="16" height="24" viewBox="0 0 16 24" fill="#fff"><path d="M4 1h4l1 6-3 2c1 3 2 5 4 7l3-2 3 4-2 4C8 23 2 14 1 5z"/></svg>
      <span>01632 960 417</span>
      <span class="gap"></span>
      <svg width="24" height="16" viewBox="0 0 24 16" fill="none" stroke="#fff" stroke-width="1.6"><rect x="1" y="1" width="22" height="14"/><path d="M1 1l11 8 11-8"/></svg>
      <span>hello@velborix-example.com</span>
    </div>
    <div class="contact-line contact-address">
      <svg width="13" height="19" viewBox="0 0 13 19" fill="#fff"><path d="M6.5 0A6.5 6.5 0 0 0 0 6.5C0 11 6.5 19 6.5 19S13 11 13 6.5A6.5 6.5 0 0 0 6.5 0zm0 9a2.5 2.5 0 1 1 0-5 2.5 2.5 0 0 1 0 5z"/></svg>
      <span>Velborix Ltd, Crest Suites, Dunmoor Road, Cheltenham, GL53 4QT</span>
    </div>
  </footer>
</main>
</body>
</html>
```